Blue Harbor Inc - Cutting-Edge Biotech Laboratory - Sleek & Sophisticated

Please design a website that has more of a high-tech and high-end feel, with contents outlined in the uploaded file.

Please have main tabs of the following categories: Home, About, FDA & LAWS, Science, Products, Media, Contact.

Media can include all the videos and photos.

Current website: www.blueharborlabs.com - it needs to be much more high-end, sleek and more organized. Please do NOT follow the outlines in the old website, but follow the uploaded CONTENT file.

Target Market(s)

doctors

Industry/Entity Type

Biotechnology

Coding

Coded - Design and coding required

Number of Pages Required

5+ page

Requirements
Must have
• Logo
Nice to have
• Some lotion on the website

```html
<!DOCTYPE html>
<html lang="en">
<head>
<meta charset="utf-8">
<title>Blue Harbor Inc</title>
<link href="https://fonts.googleapis.com/css2?family=Lato:ital,wght@0,400;0,700;0,900;1,400&family=Open+Sans:wght@400;600&display=swap" rel="stylesheet">
<style>
:root{
  --ink:#1c1c1c;
  --muted:#6b6b6b;
  --gold:#b49a6a;
  --gold-dark:#8a7650;
  --band:#37332b;
  --team-bg:#ececec;
  --footer:#2d2d2d;
  --footer-bottom:#1d1d1d;
  --white:#ffffff;
  --hero-a:#0a1a22;
  --hero-b:#1d3b3c;
}
*{margin:0;padding:0;box-sizing:border-box}
html,body{width:1200px;height:2542px;overflow:hidden;background:var(--white)}
body{position:relative;font-family:'Open Sans',Arial,sans-serif;color:var(--ink)}
.abs{position:absolute}

/* header */
.site-header{position:absolute;left:0;top:0;width:1200px;height:105px;background:var(--white)}
.brand{left:100px;top:28px;font-family:'Lato',sans-serif;font-weight:900;font-size:32px;color:#3a3a3a;letter-spacing:.5px}
.top-contact{top:26px;right:100px;display:flex;gap:30px;font-size:14px;color:#333;align-items:center}
.top-contact span{display:flex;align-items:center;gap:10px}
.main-nav{top:62px;left:593px;font-family:'Lato',sans-serif;font-size:16px;color:#222}
.main-nav a{position:absolute;top:0;white-space:nowrap;color:inherit;text-decoration:none}
.main-nav a.active{color:var(--gold-dark)}

/* hero */
.hero{left:0;top:105px;width:1200px;height:575px}
.hero-title{left:634px;top:222px;font-family:'Lato',sans-serif;font-weight:700;font-size:86px;color:var(--white);line-height:1}
.hero-sub{left:634px;top:338px;font-family:'Open Sans',sans-serif;font-weight:600;font-size:29px;line-height:39px;color:var(--white)}
.btn-outline-light{left:637px;top:449px;width:155px;height:45px;border:2px solid var(--white);border-radius:23px;color:var(--white);font-weight:600;font-size:17px;display:flex;align-items:center;justify-content:center}
.hero-dots{left:571px;top:589px;display:flex;gap:7px}
.hero-dots i{width:10px;height:10px;border:1.5px solid var(--white);border-radius:50%;display:block}
.hero-dots i.on{background:var(--white)}

/* about */
.section-title{font-family:'Lato',sans-serif;font-size:31px;color:var(--ink)}
.about-title{left:100px;top:745px}
.about-text{left:100px;top:800px;width:478px;font-size:14.5px;line-height:30px;color:var(--muted);text-align:justify}
.btn-outline-dark{left:100px;top:971px;width:107px;height:38px;border:2px solid #222;border-radius:20px;font-weight:600;font-size:14px;display:flex;align-items:center;justify-content:center}
.video-frame{left:627px;top:754px;width:475px;height:258px;border:3px solid #e4e4e4;background:linear-gradient(135deg,#6a5a3c,#a8884c 45%,#5c4a32)}
.video-caption{left:627px;top:1017px;font-size:13px;color:#222}

/* applications band */
.apps-band{left:0;top:1086px;width:1200px;height:363px;background:var(--band)}
.apps-title{left:0;top:1155px;width:1200px;text-align:center;font-family:'Lato',sans-serif;font-size:30px;color:var(--white)}
.app{top:1215px;width:200px;margin-left:-100px;text-align:center}
.app svg{display:block;margin:0 auto}
.app-label{margin-top:16px;font-family:'Lato',sans-serif;font-size:22px;color:var(--white)}
.band-pointer{left:575px;top:1448px}

/* intro text */
.intro-text{left:230px;top:1515px;width:740px;text-align:center;font-size:14.5px;line-height:30px;color:var(--muted)}
.link-details{left:0;top:1621px;width:1200px;text-align:center;font-size:14px;color:#222;text-decoration:underline}

/* team */
.team{left:0;top:1717px;width:1200px;height:458px;background:linear-gradient(160deg,#f2f2f2,#e2e2e2 50%,#efefef)}
.team-title{left:0;top:1782px;width:1200px;text-align:center}
.member{top:1857px;width:260px;margin-left:-130px;text-align:center}
.portrait{width:150px;height:150px;border-radius:50%;border:3px solid #d9d9d9;margin:0 auto}
.member-name{margin-top:22px;font-family:'Lato',sans-serif;font-style:italic;font-size:14px;color:#333;text-transform:uppercase}
.member-role{margin-top:6px;font-family:'Lato',sans-serif;font-size:18px;line-height:27px;color:#222}
.team-arrow{top:1922px}

/* footer */
.site-footer{left:0;top:2175px;width:1200px;height:317px;background:var(--footer)}
.footer-heading{top:2245px;font-family:'Lato',sans-serif;font-size:22px;color:var(--white)}
.footer-list{top:2295px;list-style:none;font-size:13.5px;line-height:24.7px;color:#e6e6e6}
.footer-list li::before{content:"";display:inline-block;width:6px;height:6px;border-radius:50%;background:#e6e6e6;margin-right:18px;vertical-align:middle}
.footer-contact{left:536px;top:2294px;width:270px;font-size:13.5px;line-height:24px;color:#e6e6e6}
.footer-contact div{display:flex;gap:16px;margin-bottom:8px}
.footer-contact svg{flex:none;margin-top:5px}
.newsletter-note{left:878px;top:2291px;width:230px;font-size:13px;line-height:21px;color:#e6e6e6}
.newsletter-field{left:878px;top:2348px;width:222px;height:31px;background:var(--white);font-size:13px;color:#888;padding:6px 10px}
.newsletter-field svg{position:absolute;right:10px;top:9px}
.footer-bottom{left:0;top:2492px;width:1200px;height:50px;background:var(--footer-bottom)}
.copyright{left:100px;top:2507px;font-size:13px;color:#e6e6e6}
.social{top:2509px;left:970px;display:flex;gap:22px}
.social i{display:block;width:14px;height:14px;border-radius:50%;background:#e6e6e6}
</style>
</head>
<body>

<header class="site-header">
  <div class="abs brand">Blue Harbor</div>
  <div class="abs top-contact">
    <span><svg width="13" height="13" viewBox="0 0 24 24"><path fill="#222" d="M6.6 10.8a15 15 0 006.6 6.6l2.2-2.2a1 1 0 011-.25 11.4 11.4 0 003.6.6 1 1 0 011 1V20a1 1 0 01-1 1A17 17 0 013 4a1 1 0 011-1h3.5a1 1 0 011 1 11.4 11.4 0 00.6 3.6 1 1 0 01-.25 1z"/></svg>5550142387</span>
    <span style="color:#ccc">|</span>
    <span><svg width="15" height="12" viewBox="0 0 24 18"><path fill="#222" d="M0 0h24v2L12 10 0 2zM0 4.5l12 8 12-8V18H0z"/></svg>info@blueharborlabs.com</span>
  </div>
  <nav class="abs main-nav">
    <a class="active" style="left:0">Home</a>
    <a style="left:68px">About</a>
    <a style="left:136px">FDA &amp; LAWS</a>
    <a style="left:249px">Science</a>
    <a style="left:327px">Products</a>
    <a style="left:414px">Contact</a>
    <a style="left:492px;top:2px"><svg width="15" height="15" viewBox="0 0 24 24"><circle cx="10" cy="10" r="7" fill="none" stroke="#222" stroke-width="3"/><path d="M15 15l7 7" stroke="#222" stroke-width="3.5"/></svg></a>
  </nav>
</header>

<svg class="abs hero" viewBox="0 0 1200 575" role="img" aria-label="Laboratory photograph: gloved hand holding a green sample against a dark background with molecular structure graphics">
  <defs>
    <linearGradient id="heroFill" x1="0" y1="0" x2="1" y2="0">
      <stop offset="0" stop-color="#3c5a44"/>
      <stop offset=".3" stop-color="#4f6b3a"/>
      <stop offset=".55" stop-color="#1a3440"/>
      <stop offset="1" stop-color="#06121a"/>
    </linearGradient>
  </defs>
  <path d="M0 0H1200V460C1020 500 780 575 520 575C300 575 140 520 0 455Z" fill="url(#heroFill)"/>
  <path d="M0 455C140 520 300 575 520 575C780 575 1020 500 1200 460" fill="none" stroke="#2a2a2a" stroke-width="3"/>
</svg>
<div class="abs hero-title">Blue Harbor</div>
<div class="abs hero-sub">Leader in Regenerative Medicine<br>Innovator of the Industry</div>
<div class="abs btn-outline-light">Contact Now!</div>
<div class="abs hero-dots"><i class="on"></i><i></i><i></i><i></i></div>

<h2 class="abs section-title about-title">About Us</h2>
<p class="abs about-text">Blue Harbor Therapy provides Non-Embryonic Stem Cells and unique protocols to doctors in order to help their patients who face major health conditions, as well as those who simply wish to stay young and healthy. Over the past seven years of development, we have successfully conducted research into major diseases related to kidney.</p>
<div class="abs btn-outline-dark">Read More</div>
<div class="abs video-frame" role="img" aria-label="Video still: interview with company owner seated in a warmly lit studio">
  <svg class="abs" style="left:210px;top:104px" width="44" height="44" viewBox="0 0 44 44"><path d="M8 4L40 22 8 40Z" fill="#fff" fill-opacity=".75"/></svg>
</div>
<div class="abs video-caption">Interview with company owner Mark Delaney on stem cells</div>

<section class="abs apps-band"></section>
<h2 class="abs apps-title">Wide variety of clinical applications</h2>

<div class="abs app" style="left:158px">
  <svg width="108" height="122" viewBox="0 0 108 122"><path d="M54 3L104 31V91L54 119 4 91V31Z" fill="none" stroke="var(--gold)" stroke-width="3"/><path d="M54 14L94 37V85L54 108 14 85V37Z" fill="#2a2620"/><circle cx="54" cy="48" r="10" fill="#fff"/><path d="M36 62H72L66 82H42Z" fill="#fff"/><path d="M44 82L40 96M64 82L68 96" stroke="#fff" stroke-width="5"/></svg>
  <div class="app-label">Orthopedics</div>
</div>
<div class="abs app" style="left:371px">
  <svg width="108" height="122" viewBox="0 0 108 122"><path d="M54 3L104 31V91L54 119 4 91V31Z" fill="none" stroke="var(--gold)" stroke-width="3"/><path d="M54 14L94 37V85L54 108 14 85V37Z" fill="#2a2620"/><rect x="32" y="52" width="26" height="34" fill="#fff"/><rect x="58" y="42" width="22" height="44" rx="3" fill="#fff"/><rect x="60" y="36" width="18" height="6" fill="#fff"/><path d="M69 56V72M61 64H77" stroke="#2a2620" stroke-width="4"/><path d="M37 62H53M37 70H53M37 78H53" stroke="#2a2620" stroke-width="2.5"/></svg>
  <div class="app-label">Sports Medicine</div>
</div>
<div class="abs app" style="left:586px">
  <svg width="108" height="122" viewBox="0 0 108 122"><path d="M54 3L104 31V91L54 119 4 91V31Z" fill="none" stroke="var(--gold)" stroke-width="3"/><path d="M54 14L94 37V85L54 108 14 85V37Z" fill="#2a2620"/><path d="M54 70C38 58 36 50 40 44 44 38 51 40 54 45 57 40 64 38 68 44 72 50 70 58 54 70Z" fill="#fff"/><path d="M30 74C40 74 46 82 56 82H74C80 82 80 88 74 88H46" fill="none" stroke="#fff" stroke-width="5" stroke-linecap="round"/></svg>
  <div class="app-label">Wound Care</div>
</div>
<div class="abs app" style="left:800px">
  <svg width="108" height="122" viewBox="0 0 108 122"><path d="M54 3L104 31V91L54 119 4 91V31Z" fill="none" stroke="var(--gold)" stroke-width="3"/><path d="M54 14L94 37V85L54 108 14 85V37Z" fill="#2a2620"/><path d="M46 46C60 44 66 56 62 72 60 84 58 96 50 96 42 96 44 82 42 70 40 58 38 48 46 46Z" fill="#fff"/><circle cx="44" cy="37" r="5" fill="#fff"/><circle cx="53" cy="36" r="3.5" fill="#fff"/><circle cx="60" cy="38" r="3" fill="#fff"/><circle cx="65" cy="42" r="2.5" fill="#fff"/></svg>
  <div class="app-label">Podiatry</div>
</div>
<div class="abs app" style="left:1014px">
  <svg width="108" height="122" viewBox="0 0 108 122"><path d="M54 3L104 31V91L54 119 4 91V31Z" fill="none" stroke="var(--gold)" stroke-width="3"/><path d="M54 14L94 37V85L54 108 14 85V37Z" fill="#2a2620"/><path d="M38 92V78C30 72 30 56 38 46 48 34 70 36 74 54L78 66H72V78H60V92Z" fill="#fff"/><circle cx="56" cy="56" r="9" fill="none" stroke="#2a2620" stroke-width="4" stroke-dasharray="4 3"/><circle cx="56" cy="56" r="3" fill="#2a2620"/></svg>
  <div class="app-label">Pain Management</div>
</div>
<svg class="abs band-pointer" width="50" height="26" viewBox="0 0 50 26"><path d="M0 0H50L25 26Z" fill="var(--band)"/></svg>

<p class="abs intro-text">Blue Harbor Inc has developed innovative processes and safety protocols, which deliver the highest cellular tissue viability and safety standards. With these safety and quality standards, Blue Harbor has become the leader of birth tissue allografts in the field of regenerative medicine.</p>
<a class="abs link-details">View details</a>

<section class="abs team"></section>
<h2 class="abs section-title team-title">Our Team</h2>
<svg class="abs team-arrow" style="left:99px" width="16" height="26" viewBox="0 0 16 26"><path d="M14 2L3 13 14 24" fill="none" stroke="#888" stroke-width="3.5"/></svg>
<svg class="abs team-arrow" style="left:1085px" width="16" height="26" viewBox="0 0 16 26"><path d="M2 2L13 13 2 24" fill="none" stroke="#888" stroke-width="3.5"/></svg>
<div class="abs member" style="left:331px">
  <div class="portrait" role="img" aria-label="Portrait photo of Mark Delaney outdoors" style="background:linear-gradient(160deg,#4d6a3a,#2f4a6a)"></div>
  <div class="member-name">Mark Delaney</div>
  <div class="member-role">Stem Cell Technology<br>Chief Scientist</div>
</div>
<div class="abs member" style="left:600px">
  <div class="portrait" role="img" aria-label="Portrait photo of Laura Benson" style="background:linear-gradient(160deg,#e0d8cc,#b8a890)"></div>
  <div class="member-name">Laura Benson</div>
  <div class="member-role">Stem Cell Project<br>Manager</div>
</div>
<div class="abs member" style="left:870px">
  <div class="portrait" role="img" aria-label="Portrait photo of Dr. Samuel R. Price" style="background:linear-gradient(160deg,#d8d4cf,#5a4a40)"></div>
  <div class="member-name">Dr. Samuel R. Price</div>
  <div class="member-role">Price Center for Cardiac<br>Longevity</div>
</div>

<footer class="abs site-footer"></footer>
<h3 class="abs footer-heading" style="left:102px">Quick Links</h3>
<ul class="abs footer-list" style="left:102px"><li>Home</li><li>About</li><li>FDA &amp; LAWS</li><li>Science</li><li>Products</li><li>Contact</li></ul>
<h3 class="abs footer-heading" style="left:312px">Other Links</h3>
<ul class="abs footer-list" style="left:312px"><li>HCT/ps</li><li>Texas Regulations</li><li>Terms Of Use</li><li>Privacy Policy</li></ul>
<h3 class="abs footer-heading" style="left:536px">Contact Us</h3>
<div class="abs footer-contact">
  <div><svg width="13" height="13" viewBox="0 0 24 24"><path d="M22 2L2 11l9 2 2 9z" fill="#e6e6e6"/></svg><span>Blue Harbor Labs, 2210 Lakeview Road, Fairmont, MI, 48000</span></div>
  <div><svg width="14" height="11" viewBox="0 0 24 18"><rect x="1" y="1" width="22" height="16" fill="none" stroke="#e6e6e6" stroke-width="2"/><path d="M1 1l11 9 11-9" fill="none" stroke="#e6e6e6" stroke-width="2"/></svg><span>info@blueharborlabs.com</span></div>
  <div><svg width="13" height="13" viewBox="0 0 24 24"><path fill="#e6e6e6" d="M6.6 10.8a15 15 0 006.6 6.6l2.2-2.2a1 1 0 011-.25 11.4 11.4 0 003.6.6 1 1 0 011 1V20a1 1 0 01-1 1A17 17 0 013 4a1 1 0 011-1h3.5a1 1 0 011 1 11.4 11.4 0 00.6 3.6 1 1 0 01-.25 1z"/></svg><span>5550142387</span></div>
</div>
<h3 class="abs footer-heading" style="left:878px">Newsletter</h3>
<p class="abs newsletter-note">Sign up our newsletter to get more information</p>
<div class="abs newsletter-field">Email address<svg width="13" height="13" viewBox="0 0 24 24"><path d="M2 12H20M12 4l8 8-8 8" fill="none" stroke="#222" stroke-width="3.5"/></svg></div>

<div class="abs footer-bottom"></div>
<div class="abs copyright">2018 © BlueHarbor. All rights reserved.</div>
<div class="abs social"><i></i><i></i><i></i><i></i></div>

</body>
</html>
```